Tolvane Inc., a third party debt collection agency needs a Website

Tolvane needs a very basic website (3 basic pages) so that consumers can download forms, potential employees can get required EEO language and see potential jobs, and to show that they are a consumer friendly organization.

I've attached a list of requirements and wishes titled "Tolvane Website Specifications"

Target Market(s)

Consumers that need to repay their government loans; Tolvane will walk through the process to assist them.

Industry/Entity Type

Financial Service

Coding

Coded - Design and coding required

Number of Pages Required

1 page

Font styles to use
Sans Serif

Colors
0355a3

Requirements
Must have
• Tolvane Logo
• See document "Tolvane Website Specifications" for all requirements

```html
<!DOCTYPE html>
<html lang="en">
<head>
<meta charset="utf-8">
<title>Careers @ Tolvane</title>
<link href="https://fonts.googleapis.com/css2?family=Open+Sans:wght@400;600;700&display=swap" rel="stylesheet">
<style>
:root{
  --navy:#252770;
  --ink:#1f2a6b;
  --deep:#0f2f5e;
  --maroon:#8b1a1f;
  --body:#444;
  --rule:#e4e4e4;
  --band:#f6f6f6;
}
*{box-sizing:border-box;margin:0;padding:0}
html,body{width:706px;height:1200px;overflow:hidden;background:#fff}
body{position:relative;font-family:"Open Sans",Arial,sans-serif;color:var(--body)}
.abs{position:absolute}
.topline{left:0;top:0;width:706px;height:2px;background:var(--navy)}
.brand{left:94px;top:38px;font-size:19px;font-weight:700;color:var(--maroon);letter-spacing:-.2px}
.contact-top{top:15px;font-size:7.5px;color:#555;display:flex;align-items:center;gap:6px}
.ring{width:15px;height:15px;border:1px solid var(--maroon);border-radius:50%;display:flex;align-items:center;justify-content:center}
.nav{top:49px;font-size:7.5px;font-weight:600;color:#333;letter-spacing:.2px}
.nav.active{color:var(--deep);font-weight:700}
.search{left:588px;top:44px;width:21px;height:21px;border-radius:50%;background:var(--navy);display:flex;align-items:center;justify-content:center}
.hero{left:0;top:74px;width:706px;height:298px;background:linear-gradient(100deg,#c9b6a4 0%,#e3e0dc 35%,#cfd4de 60%,#9aa4b4 100%)}
.hero-label{right:0;top:133px;width:250px;height:28px;background:rgba(40,40,45,.85);clip-path:polygon(4% 0,100% 0,100% 100%,0 100%);color:#fff;font-size:11px;font-weight:700;padding:6px 0 0 23px;letter-spacing:.3px}
.hero svg{position:absolute;left:0;top:0}
h1.page-title{left:0;width:706px;top:378px;text-align:center;font-size:18px;font-weight:700;color:var(--deep)}
.red{color:var(--maroon)}
.rule{left:94px;width:517px;height:1px;background:var(--rule)}
h2{font-size:14px;font-weight:700;color:var(--ink)}
h3{font-size:9px;font-weight:600;color:var(--ink)}
.field{top:453px;height:22px;background:#f1f1f1;border:1px solid #ddd;font-size:6px;color:#555;padding:7px 9px}
.eeo-line{left:94px;top:486px;font-size:8.5px;font-weight:700;color:var(--ink)}
.p{font-size:6.2px;line-height:11px;color:#444}
.info{left:94px;font-size:6.5px;color:#444;display:flex;gap:8px;align-items:flex-start}
.dot{width:13px;height:13px;border-radius:50%;background:var(--deep);flex:none;display:flex;align-items:center;justify-content:center}
.photo{left:374px;top:439px;width:237px;height:159px;border:1px solid #ddd;padding:2px;background:#fff}
.photo div{width:100%;height:100%;background:linear-gradient(110deg,#8fa3b5,#e1e6ec 45%,#c4ccd6)}
.btn{height:18px;display:flex;font-size:6px;font-weight:600;color:#fff;letter-spacing:.2px}
.btn span{background:var(--maroon);display:flex;align-items:center;padding:0 10px;flex:1}
.btn i{width:19px;background:var(--navy);display:flex;align-items:center;justify-content:center}
.band{left:0;top:944px;width:706px;height:116px;background:var(--band);border-top:1px solid #e2e2e2}
.band .divider{left:352px;top:0;width:1px;height:116px;background:#ddd}
.partner{top:31px;width:353px;text-align:center;font-size:8.5px;font-weight:600;color:var(--ink)}
.footer{left:0;top:1060px;width:706px;height:108px;background:var(--navy);color:#fff}
.footer .brand-f{left:94px;top:55px;font-size:19px;font-weight:700;color:#fff}
.footer .vline{top:18px;width:1px;height:78px;background:rgba(255,255,255,.15)}
.footer h4{font-size:8.5px;font-weight:600}
.footer .link{font-size:6.5px}
.footer .ci{font-size:6.3px;display:flex;gap:7px;align-items:flex-start;line-height:11px}
.bottom{left:0;top:1168px;width:706px;height:32px;background:var(--maroon);color:#fff;font-size:6px;text-align:center;padding-top:11px}
</style>
</head>
<body>
<div class="abs topline"></div>
<div class="abs brand">Tolvane, Inc.</div>
<div class="abs contact-top" style="left:400px"><span class="ring"><svg width="7" height="6"><rect x="0" y="0" width="7" height="6" fill="#8b1a1f"/></svg></span>Email: info@company.Com</div>
<div class="abs contact-top" style="left:520px"><span class="ring"><svg width="7" height="7" viewBox="0 0 10 10"><path d="M2 1l2 2-1 1.5c.6 1.3 1.2 1.9 2.5 2.5L7 6l2 2-1.5 1.5C4.5 9 1 5.5.5 2z" fill="#8b1a1f"/></svg></span>Phone: 000-000-0009</div>
<div class="abs nav" style="left:255px">HOME</div>
<div class="abs nav" style="left:305px">CONSUMER INFORMATION</div>
<div class="abs nav active" style="left:429px">CAREERS @ TOLVANE
  <svg width="28" height="5" style="position:absolute;left:26px;top:12px"><path d="M1 4Q14 -1 27 3" stroke="#252770" stroke-width="1.2" fill="none"/></svg></div>
<div class="abs nav" style="left:537px">CONTACT</div>
<div class="abs search"><svg width="8" height="8" viewBox="0 0 10 10"><circle cx="4" cy="4" r="3" stroke="#fff" stroke-width="1.6" fill="none"/><path d="M6.3 6.3L9 9" stroke="#fff" stroke-width="1.6"/></svg></div>

<div class="abs hero" role="img" aria-label="Photo of a smiling team of colleagues in an office">
  <svg width="706" height="298" viewBox="0 0 706 298">
    <path d="M0 254C110 305 250 300 360 290S600 252 706 246V298H0Z" fill="#fff"/>
    <path d="M0 254C110 305 250 300 360 290S600 252 706 246" stroke="#252770" stroke-width="3" fill="none"/>
  </svg>
  <div class="abs hero-label">CAREERS @ TOLVANE</div>
</div>

<h1 class="abs page-title">Careers @ <span class="red">Tolvane</span></h1>
<div class="abs rule" style="top:415px"></div>

<h2 class="abs" style="left:94px;top:425px">Information about <span class="red">Available Jobs</span></h2>
<div class="abs field" style="left:94px;width:123px">Job Title</div>
<div class="abs field" style="left:222px;width:131px">No.of positions at a time
  <svg width="5" height="8" style="position:absolute;right:8px;top:7px"><path d="M0 3L2.5 0 5 3M0 5l2.5 3L5 5" fill="#888"/></svg></div>
<div class="abs eeo-line">Tolvane is an Equal <span class="red">Employment Opportunity employer.</span></div>
<p class="abs p" style="left:94px;top:504px;width:265px">If you need to contact us regarding the accessibility of our website or need assistance completing the application process, please contact us using the contact information below:</p>
<div class="abs info" style="top:535px"><span class="dot"><svg width="6" height="6" viewBox="0 0 10 10"><path d="M2 1l2 2-1 1.5c.6 1.3 1.2 1.9 2.5 2.5L7 6l2 2-1.5 1.5C4.5 9 1 5.5.5 2z" fill="#fff"/></svg></span><span style="line-height:11px">Main Office Address # Lorem ipsmdummy street,<br>Dummy Address 972, dummy name</span></div>
<div class="abs info" style="top:563px"><span class="dot"><svg width="6" height="6" viewBox="0 0 10 10"><path d="M2 1l2 2-1 1.5c.6 1.3 1.2 1.9 2.5 2.5L7 6l2 2-1.5 1.5C4.5 9 1 5.5.5 2z" fill="#fff"/></svg></span><span style="padding-top:2px">Main Office Contact # 555-310-4872</span></div>
<div class="abs info" style="top:580px"><span class="dot"><svg width="6" height="6"><rect x="0" y="1" width="6" height="4" fill="#fff"/></svg></span><span style="padding-top:2px">Main Office Fax # 555-310-4873</span></div>
<div class="abs info" style="top:596px"><span class="dot"><svg width="6" height="5"><path d="M0 0h6v5H0zM0 0l3 2.5L6 0" fill="#fff" stroke="#0f2f5e" stroke-width=".6"/></svg></span><span style="padding-top:2px">Application Email jobs@tolvane.com</span></div>
<div class="abs photo"><div role="img" aria-label="Photo of call centre staff wearing headsets at their desks"></div></div>

<div class="abs rule" style="top:632px"></div>

<h2 class="abs" style="left:96px;top:652px">Application <span class="red">Form</span></h2>
<h3 class="abs" style="left:94px;top:677px">Tolvane Employment Application</h3>
<p class="abs p" style="left:94px;top:694px;width:240px">Sed ut perspiciatis unde omnis iste natus error sit voluptatem accusantium dol oremque laudantium, totam rem aperiam, ea que ipsa quae ab illo inventore verit atis et quasi architectobea tae vitae dicta sunt explicaboemo enim ipsam voluptaed ut perspiciatis unde omnis iste natus error sit voluptatem accusantium doloremlo que laudantium, totam rem aperiam, ea que ipsa quae ab illo inventore verit.</p>
<div class="abs btn" style="left:94px;top:758px;width:115px"><span>DOWNLOAD APPLICATION</span><i><svg width="7" height="7"><circle cx="3.5" cy="3.5" r="3.5" fill="#fff"/><path d="M2.7 2l1.5 1.5-1.5 1.5" stroke="#252770" fill="none"/></svg></i></div>

<h2 class="abs" style="left:372px;top:652px">EEO <span class="red">Statement</span></h2>
<h3 class="abs" style="left:372px;top:677px">Employment Opportunity is The Law</h3>
<p class="abs p" style="left:372px;top:694px;width:240px">Sed ut perspiciatis unde omnis iste natus error sit voluptatem accusantium dol oremque laudantium, totam rem aperiam, ea que ipsa quae ab illo inventore verit atis et quasi architectobea tae vitae dicta sunt explicaboemo enim ipsam voluptaed ut perspiciatis unde omnis iste natus error sit voluptatem accusantium doloremlo que laudantium, totam rem aperiam, ea que ipsa quae ab illo inventore verit.</p>
<div class="abs btn" style="left:372px;top:758px;width:89px"><span>STATEMENT EEO</span><i><svg width="7" height="7"><circle cx="3.5" cy="3.5" r="3.5" fill="#fff"/><path d="M2.7 2l1.5 1.5-1.5 1.5" stroke="#252770" fill="none"/></svg></i></div>

<div class="abs rule" style="top:804px"></div>

<h2 class="abs" style="left:0;width:706px;text-align:center;top:825px">Our <span class="red">Documents</span></h2>
<p class="abs p" style="left:110px;top:851px;width:486px;text-align:center">Sed ut perspiciatis unde omnis iste natus error sit voluptatem accusantium doloremque laudantium, totam rem aperiam, eaque ipsa quae ab illo inventore veritatis et quasi architecto beatae vitae dicta sunt explicabo. Nemo enim ipsam voluptatem quia voluptas sit aspernatur aut odit aut fugiSed ut perspiciatis unde omnis iste natus error sit voluptatem accusantium doloremque laudantium, totam rem aperiam, eaque ipsa quae ab illo inventore veritatis et quasi architecto beatae vitae</p>
<div class="abs btn" style="left:152px;top:901px;width:127px"><span style="justify-content:center">EEO AA M/F/VET/DISABILITY</span><i><svg width="7" height="7"><circle cx="3.5" cy="3.5" r="3.5" fill="#fff"/><path d="M2.7 2l1.5 1.5-1.5 1.5" stroke="#252770" fill="none"/></svg></i></div>
<div class="abs btn" style="left:285px;top:901px;width:132px"><span style="justify-content:center">YOUR RIGHTS AS AN APPLICANT</span><i><svg width="7" height="7"><circle cx="3.5" cy="3.5" r="3.5" fill="#fff"/><path d="M2.7 2l1.5 1.5-1.5 1.5" stroke="#252770" fill="none"/></svg></i></div>
<div class="abs btn" style="left:422px;top:901px;width:132px"><span style="justify-content:center">WE PARTICIPATE IN WORKCHECK</span><i><svg width="7" height="7"><circle cx="3.5" cy="3.5" r="3.5" fill="#fff"/><path d="M2.7 2l1.5 1.5-1.5 1.5" stroke="#252770" fill="none"/></svg></i></div>

<div class="abs band">
  <div class="abs divider"></div>
  <div class="abs partner" style="left:0">Tolvane is accredited the Fair Trade Council</div>
  <div class="abs" style="left:170px;top:57px;width:71px;height:27px;border-radius:4px;background:#1d5a6e"></div>
  <div class="abs partner" style="left:353px">Tolvane is a member of Collectors Guild International</div>
  <div class="abs" style="left:449px;top:55px;width:27px;height:27px;background:#3a78b8"></div>
</div>

<div class="abs footer">
  <div class="abs brand-f">Tolvane, Inc.</div>
  <div class="abs vline" style="left:256px"></div>
  <div class="abs vline" style="left:446px"></div>
  <h4 class="abs" style="left:310px;top:22px">NAVIGATION</h4>
  <div class="abs link" style="left:311px;top:43px">Home</div>
  <div class="abs link" style="left:311px;top:56px">Consumer Information</div>
  <div class="abs link" style="left:311px;top:69px">Careers @ Tolvane</div>
  <div class="abs link" style="left:311px;top:82px">Contact</div>
  <h4 class="abs" style="left:504px;top:22px">CONTACT US</h4>
  <div class="abs ci" style="left:504px;top:42px"><svg width="5" height="7" viewBox="0 0 10 14"><path d="M5 0a5 5 0 0 1 5 5c0 4-5 9-5 9S0 9 0 5a5 5 0 0 1 5-5z" fill="#fff"/></svg><span>201 lorem ipsum dolor site,<br>tolvane dummy text.5482</span></div>
  <div class="abs ci" style="left:504px;top:65px"><svg width="6" height="6" viewBox="0 0 10 10"><path d="M2 1l2 2-1 1.5c.6 1.3 1.2 1.9 2.5 2.5L7 6l2 2-1.5 1.5C4.5 9 1 5.5.5 2z" fill="#fff"/></svg><span>Phone:&nbsp; 555-204-7719</span></div>
  <div class="abs ci" style="left:504px;top:77px"><svg width="6" height="5"><rect width="6" height="5" fill="#fff"/></svg><span>info@tolvane.com</span></div>
</div>
<div class="abs bottom">© 2016 Tolvane. All copyrights are reserved&nbsp; Term of Use, Privay Policy</div>
</body>
</html>
```